Hvac and insulation company needs good looking business card design

We are hvac and insulation company and looking for a new business cards that look to today standards designs

Target Market(s)

homeowners

Industry/Entity Type

Hvac

Contact Information for Business Card

Name: Walter Brinoku
Home comfort consultant
address: 4827 Dunmore St #215 Oakland, CA 94619
office: 888-316-2790
cell: 510-742-3185
Lic.# 584261
Email: walter@corvane-hvac.com
Web: corvane-hvac.com

Requirements
Must have
• clean and sleek look
Nice to have
• simple with a clean look
Should not have
• to busy business card

```html
<!DOCTYPE html>
<html lang="en">
<head>
<meta charset="utf-8">
<title>Corvane Business Card</title>
<link href="https://fonts.googleapis.com/css2?family=Lato:wght@400;700&display=swap" rel="stylesheet">
<style>
  :root {
    --orange: #f58220;
    --ink: #6d6e70;
    --ink-soft: #7a7b7d;
    --paper: #ffffff;
    --backdrop: #2b4a6d;
  }
  * { margin: 0; padding: 0; box-sizing: border-box; }
  html, body {
    width: 1200px; height: 1000px; overflow: hidden;
    background: var(--backdrop);
    font-family: "Lato", Arial, sans-serif;
  }
  .sheet {
    position: relative; width: 1200px; height: 1000px;
  }
  .card {
    position: absolute; left: 220px; width: 760px; height: 435px;
    background: var(--paper);
    overflow: hidden;
  }
  .card--front { top: 40px; }
  .card--back { top: 525px; }

  /* front */
  .brand-block {
    position: absolute; left: 58px; top: 118px;
    width: 196px; height: 196px; background: var(--orange);
  }
  .brand-name {
    position: absolute; color: var(--orange); font-weight: 700;
    letter-spacing: 0.5px; line-height: 1;
  }
  .card--front .brand-name { left: 410px; top: 178px; font-size: 54px; }
  .website {
    position: absolute; right: 67px; top: 380px;
    font-size: 23px; color: var(--ink);
  }

  /* back */
  .card--back .brand-name { right: 30px; top: 48px; font-size: 56px; }
  .person-name {
    position: absolute; left: 39px; top: 120px;
    font-size: 42px; color: var(--ink); font-weight: 400;
  }
  .person-role {
    position: absolute; left: 39px; top: 170px;
    font-size: 23px; color: var(--ink);
  }
  .divider { position: absolute; left: 39px; top: 212px; }
  .address {
    position: absolute; right: 35px; top: 218px;
    font-size: 20px; color: #fff; line-height: 26px;
  }
  .contacts {
    position: absolute; left: 39px; top: 262px; list-style: none;
  }
  .contacts li {
    display: flex; align-items: center; gap: 16px;
    font-size: 27px; color: var(--ink); height: 38px;
  }
  .contacts svg { width: 22px; height: 22px; fill: var(--ink); flex: none; }
  .license {
    position: absolute; right: 32px; top: 368px;
    font-size: 20px; color: var(--ink-soft);
  }
</style>
</head>
<body>
<main class="sheet">
  <section class="card card--front" aria-label="Card front">
    <div class="brand-block"></div>
    <div class="brand-name">corvane</div>
    <div class="website">www.corvane-hvac.com</div>
  </section>

  <section class="card card--back" aria-label="Card back">
    <div class="brand-name">corvane</div>
    <h1 class="person-name">Walter Brinoku</h1>
    <p class="person-role">Home comfort consultant</p>
    <svg class="divider" width="721" height="38" viewBox="0 0 721 38" aria-hidden="true">
      <line x1="0" y1="1" x2="200" y2="1" stroke="var(--orange)" stroke-width="2"/>
      <path d="M193 0 H721 V38 H215 Q205 38 201 28 Z" fill="var(--orange)"/>
    </svg>
    <p class="address">4827 Dunmore St #215 Oakland, CA 94619</p>
    <ul class="contacts">
      <li>
        <svg viewBox="0 0 24 24" aria-label="Office"><path d="M2 8c0-3 4-5 10-5s10 2 10 5v2h-5V8c-1-1-3-1-5-1s-4 0-5 1v2H2zM6 11h12l3 9H3zM12 13a3 3 0 1 0 0 6 3 3 0 0 0 0-6z"/></svg>
        <span>888-316-2790</span>
      </li>
      <li>
        <svg viewBox="0 0 24 24" aria-label="Cell"><path d="M6.6 10.8a15 15 0 0 0 6.6 6.6l2.2-2.2c.3-.3.7-.4 1-.2 1.1.4 2.3.6 3.6.6.6 0 1 .4 1 1V20c0 .6-.4 1-1 1A17 17 0 0 1 3 4c0-.6.4-1 1-1h3.5c.6 0 1 .4 1 1 0 1.3.2 2.5.6 3.6.1.3 0 .7-.2 1z"/></svg>
        <span>510-742-3185</span>
      </li>
      <li>
        <svg viewBox="0 0 24 24" aria-label="Email"><path d="M2 6h20v13H2zm2 1.5 8 6 8-6z" /></svg>
        <span>walter@corvane-hvac.com</span>
      </li>
    </ul>
    <p class="license">Lic.# 584261</p>
  </section>
</main>
</body>
</html>
```